Robotic Physical Therapy office needs a Grand Opening Flyer

We need a Grand Opening flyer design for a robotic physical therapy office named Kinetic Harbor Wellness. We would like it to have a clean, classy, upscale feeling that gives potential clients a V.I.P. feeling. We would like to use the colors black, gray, and yellow (logo will be uploaded).

Event: Thursday, June 1st, 2023 from 12pm-6pm
location: 58274 Pellham Ave, Bloomfield Hills, MI 48519

Industry/Entity Type

Physical therapy

Font styles to use
Script

Colors

Designer to choose colors to be used in the design.

Requirements
Nice to have
• More of a vip feel for the invite

```html
<!DOCTYPE html>
<html lang="en">
<head>
<meta charset="utf-8">
<title>Kinetic Harbor Wellness – Grand Opening</title>
<link rel="stylesheet" href="https://fonts.googleapis.com/css2?family=Great+Vibes&family=Libre+Baskerville&family=Montserrat:wght@500;700&display=swap">
<style>
  :root {
    --paper: #ffffff;
    --gold: #e2c63a;
    --gold-bright: #f4dd34;
    --gold-pale: #f8eda6;
    --ink: #111111;
    --charcoal: #3a3a42;
    --silver-light: #e6e6e9;
    --silver-dark: #8f8f95;
  }
  * { margin: 0; padding: 0; box-sizing: border-box; }
  html, body { width: 956px; height: 1200px; overflow: hidden; background: var(--paper); }
  .flyer { position: relative; width: 956px; height: 1200px; background: var(--paper); overflow: hidden; font-family: "Montserrat", sans-serif; }

  .ribbon-art {
    position: absolute; left: 0; top: 0; width: 225px; height: 1200px;
    background: linear-gradient(90deg, var(--gold-bright) 0%, var(--gold) 45%, var(--gold-pale) 100%);
    border-radius: 0 110px 110px 0;
  }
  .scissors-art {
    position: absolute; left: 120px; top: 790px; width: 230px; height: 240px;
    background: linear-gradient(135deg, var(--silver-light), var(--silver-dark));
    border-radius: 40px;
  }

  .brand { position: absolute; top: 62px; right: 46px; display: flex; align-items: center; gap: 16px; }
  .brand-dot { width: 46px; height: 46px; border-radius: 50%; background: var(--gold); }
  .brand-name { font-weight: 700; color: var(--charcoal); text-align: right; line-height: 1.05; text-transform: uppercase; font-size: 34px; }
  .brand-name span { display: block; }

  .title-grand { position: absolute; top: 244px; left: 500px; font-family: "Libre Baskerville", serif; font-weight: 400; font-size: 64px; letter-spacing: 0.32em; color: var(--ink); }
  .title-opening { position: absolute; top: 256px; left: 238px; font-family: "Great Vibes", cursive; font-size: 250px; line-height: 1; color: var(--gold); }

  .gallery { position: absolute; top: 595px; left: 283px; }
  .gallery-item { position: absolute; top: 0; width: 193px; height: 193px; }
  .gallery-item:nth-child(1) { left: 0; }
  .gallery-item:nth-child(2) { left: 222px; }
  .gallery-item:nth-child(3) { left: 445px; }
  .gallery-photo { width: 193px; height: 193px; border-radius: 50%; border: 9px solid var(--gold); background: radial-gradient(circle at 45% 40%, #e8eaee, #9aa3ae 70%, #5b6470); }
  .gallery-item:nth-child(2) .gallery-photo { background: radial-gradient(circle at 50% 45%, #a7a9b3, #4b4d57 70%, #26272d); }
  .gallery-dot { position: absolute; left: 160px; top: 142px; width: 34px; height: 34px; border-radius: 50%; background: var(--gold-bright); }
  .gallery-shadow { position: absolute; left: 12px; top: 196px; width: 170px; height: 10px; border-radius: 50%; background: radial-gradient(ellipse, rgba(0,0,0,0.22), rgba(0,0,0,0) 70%); }

  .details { position: absolute; right: 36px; text-align: right; font-size: 30px; font-weight: 500; line-height: 38px; color: var(--ink); }
  .details .label { color: var(--gold); }
  .details-event { top: 983px; }
  .details-location { top: 1110px; }
  .details-rule { position: absolute; inset: 0; }
</style>
</head>
<body>
<main class="flyer">
  <div class="ribbon-art" role="img" aria-label="Illustration of a flowing yellow ceremonial ribbon"></div>
  <div class="scissors-art" role="img" aria-label="Illustration of silver scissors cutting the ribbon"></div>

  <header class="brand">
    <span class="brand-dot"></span>
    <h1 class="brand-name"><span>Kinetic Harbor</span><span>Wellness</span></h1>
  </header>

  <div class="title-opening">Opening</div>
  <h2 class="title-grand">GRAND</h2>

  <section class="gallery">
    <figure class="gallery-item">
      <div class="gallery-photo" role="img" aria-label="Photo of a therapist assisting a client using a robotic arm-rehabilitation device"></div>
      <span class="gallery-dot"></span><span class="gallery-shadow"></span>
    </figure>
    <figure class="gallery-item">
      <div class="gallery-photo" role="img" aria-label="Close-up photo of a knee wearing a hinged orthopedic brace"></div>
      <span class="gallery-dot"></span><span class="gallery-shadow"></span>
    </figure>
    <figure class="gallery-item">
      <div class="gallery-photo" role="img" aria-label="Photo of a therapist helping a client in a robotic walking-assist machine"></div>
      <span class="gallery-dot"></span><span class="gallery-shadow"></span>
    </figure>
  </section>

  <svg class="details-rule" width="956" height="1200" viewBox="0 0 956 1200" aria-hidden="true">
    <path d="M920 975 L542 975 L518 1058" fill="none" stroke="var(--gold)" stroke-width="1.5"/>
    <path d="M920 1101 L435 1101 L410 1183" fill="none" stroke="var(--gold)" stroke-width="1.5"/>
  </svg>
  <p class="details details-event"><span class="label">Event:</span> Thursday, June<br>1st, 2023 from 12pm-6pm</p>
  <p class="details details-location"><span class="label">location:</span> 58274 Pellham Ave,<br>Bloomfield Hills, MI 48519</p>
</main>
</body>
</html>
```